Poetry Book Cover Design Project

Looking for a minimalistic book cover design for a collection of poems. The book title is "Before The Lanterns Drift Away Slowly". There are three parts to the book. First covers poetry in the theme of Rage. Second love and desire. The third is strange poems. Essentially the sections are "Rage", "Desire" and the "Strange". The reason for the title "Before The Lanterns Drift Away Slowly" is as if someone is writing these till life changes towards the intended outcome as felt in each poem. I want to have the author's name "Ruvinath Kolongaswe" at the bottom. Ilustration attached.
- Minimalistic

```html
<!DOCTYPE html>
<html lang="en">
<head>
<meta charset="utf-8">
<title>Before The Lanterns Drift Away Slowly — Ruvinath Kolongaswe</title>
<link href="https://fonts.googleapis.com/css2?family=Crimson+Pro:wght@400;700&display=swap" rel="stylesheet">
<style>
  :root {
    --paper: #ffffff;
    --frame: #cfcfcf;
    --title-blue: #2c5fab;
    --author-ink: #1a1a1a;
    --petal-yellow: #f6d51f;
    --petal-deep: #e9b80c;
    --stem-brown: #7a5a3c;
    --leaf-green: #4f7a2e;
  }
  html, body {
    margin: 0;
    padding: 0;
    width: 802px;
    height: 1200px;
    overflow: hidden;
    background: var(--paper);
  }
  .book-cover {
    position: relative;
    width: 802px;
    height: 1200px;
    box-sizing: border-box;
    border: 2px solid var(--frame);
    background: var(--paper);
    overflow: hidden;
  }
  .cover-title {
    position: absolute;
    top: 14px;
    right: 44px;
    margin: 0;
    font-family: "Crimson Pro", "Times New Roman", serif;
    font-weight: 400;
    font-size: 82px;
    line-height: 92px;
    color: var(--title-blue);
    text-align: right;
    letter-spacing: 0.5px;
  }
  .cover-title span {
    display: block;
  }
  .cover-flower {
    position: absolute;
    left: 66px;
    top: 578px;
    width: 250px;
    height: 620px;
    border-radius: 125px 125px 0 0;
    background: linear-gradient(
      180deg,
      var(--petal-yellow) 0%,
      var(--petal-deep) 34%,
      var(--leaf-green) 52%,
      var(--stem-brown) 100%
    );
    opacity: 0.9;
  }
  .cover-author {
    position: absolute;
    right: 44px;
    bottom: 88px;
    margin: 0;
    font-family: "Crimson Pro", "Times New Roman", serif;
    font-weight: 700;
    font-size: 31px;
    color: var(--author-ink);
    letter-spacing: 0.3px;
  }
</style>
</head>
<body>
  <main class="book-cover">
    <h1 class="cover-title">
      <span>Before</span>
      <span>The</span>
      <span>Lanterns</span>
      <span>Drift</span>
      <span>Away</span>
      <span>Slowly</span>
    </h1>
    <div class="cover-flower" role="img" aria-label="Photograph of a single yellow chrysanthemum on a bare brown twig with two green leaves"></div>
    <p class="cover-author">Ruvinath Kolongaswe</p>
  </main>
</body>
</html>
```